Business Card Design and Logo Needed

I need Business Cards and a Logo for my website and public speaking business which can be found at: www.corvina-lett.example

I'm looking for creative and unique ideas. Some business cards I've found online that I like can be found at:
http://gigbarrow.example/general/18-smokin-hot-business-card-designs/

and at

http://www.plumquarry.example/2009/04/50-creative-business-cards-of-50-graphic-designers/

```html
<!DOCTYPE html>
<html lang="en">
<head>
<meta charset="utf-8">
<title>Corvina Lett — Business Card</title>
<link rel="stylesheet" href="https://fonts.googleapis.com/css2?family=Questrial&family=Great+Vibes&display=swap">
<style>
  :root {
    --paper: #ffffff;
    --ink: #111111;
    --green: #66ff33;
    --blue: #0066ff;
    --purple: #9900ff;
  }
  html, body {
    margin: 0;
    padding: 0;
    width: 780px;
    height: 1200px;
    overflow: hidden;
    background: var(--paper);
  }
  .card {
    position: relative;
    width: 780px;
    height: 1200px;
    background: var(--paper);
  }
  .roles {
    position: absolute;
    right: 74px;
    top: 228px;
    margin: 0;
    padding: 0;
    list-style: none;
    text-align: right;
    font-family: "Questrial", "Century Gothic", sans-serif;
    font-size: 82px;
    line-height: 110px;
    letter-spacing: 0.5px;
  }
  .role--speaker { color: var(--green); }
  .role--philanthropist { color: var(--blue); }
  .role--author { color: var(--purple); }
  .name {
    position: absolute;
    left: 36px;
    right: 36px;
    top: 820px;
    margin: 0;
    text-align: center;
    font-family: "Great Vibes", cursive;
    font-weight: 400;
    font-size: 140px;
    line-height: 1.2;
    color: var(--ink);
  }
</style>
</head>
<body>
  <main class="card">
    <ul class="roles">
      <li class="role role--speaker">Speaker</li>
      <li class="role role--philanthropist">Philanthropist</li>
      <li class="role role--author">Author</li>
    </ul>
    <h1 class="name">Corvina Lett</h1>
  </main>
</body>
</html>
```